TK Stationery - Modern Contemporary

Develop modern template for Letterhead and Stationery (business card, letterhead, envelopes) using the TK Logo and Icon

Colors
0054AA
0677BA
7BADD7
CADEEF
E8F1F8
00AB8E
00BBA5
67D7C9
C6EFE9
E9F9F6
EE7325
F08F49
F5BC92
FAE3D3
FDF4ED
6B429C
8869AF
B7A5CE
E3DAEB
F3F0F8

```html
<!DOCTYPE html>
<html lang="en">
<head>
<meta charset="utf-8">
<title>Tavi Kora Letterhead</title>
<link href="https://fonts.googleapis.com/css2?family=Questrial&family=Arimo:wght@400&display=swap" rel="stylesheet">
<style>
  :root {
    --backdrop: #cdcccd;
    --paper: #ffffff;
    --navy: #2a3150;
    --green: #3db475;
    --orange: #ee7325;
    --ink: #555555;
    --sign-tone: #e6e6e8;
  }
  * { box-sizing: border-box; margin: 0; padding: 0; }
  html, body { width: 1173px; height: 1200px; overflow: hidden; background: var(--backdrop); }
  .letterhead {
    position: absolute; left: 230px; top: 96px;
    width: 713px; height: 1008px;
    background: var(--paper);
  }
  .brand {
    position: absolute; top: 46px; left: 0; width: 100%;
    display: flex; justify-content: center; align-items: center; gap: 8px;
  }
  .brand-dot { width: 9px; height: 9px; border-radius: 50%; background: var(--orange); }
  .brand-name {
    font-family: "Questrial", sans-serif; font-size: 34px; color: var(--navy);
    letter-spacing: 1px; line-height: 1;
  }
  .salutation {
    position: absolute; left: 66px; top: 309px;
    font-family: "Questrial", sans-serif; font-weight: 700; font-size: 17px; color: var(--ink);
    -webkit-text-stroke: 0.4px var(--ink);
  }
  .letter-body {
    position: absolute; left: 64px; top: 356px; width: 582px;
    font-family: "Arimo", Arial, sans-serif; font-size: 11.6px; line-height: 14.7px;
    color: var(--ink); text-align: justify;
  }
  .letter-body p { margin-bottom: 12.5px; }
  .closing {
    position: absolute; left: 65px; top: 659px;
    font-family: "Questrial", sans-serif; font-size: 9.5px; color: var(--ink);
    -webkit-text-stroke: 0.3px var(--ink);
  }
  .signature {
    position: absolute; left: 65px; top: 701px; width: 117px; height: 35px;
    background: linear-gradient(90deg, var(--sign-tone), #f4f4f5);
    border-radius: 4px;
  }
  .footer-rule {
    position: absolute; left: 67px; top: 917px; width: 578px; height: 1px; background: var(--navy);
  }
  .contact-list, .address {
    position: absolute; top: 928px; list-style: none;
    font-family: "Arimo", Arial, sans-serif; font-size: 11.6px; line-height: 14.5px; color: var(--navy);
  }
  .contact-list { left: 67px; }
  .contact-list li { display: flex; align-items: center; gap: 8px; }
  .contact-list svg { width: 9px; height: 9px; }
  .address { right: 68px; text-align: right; }
  .brand-band { position: absolute; top: 997px; height: 11px; }
  .brand-band.navy { left: 0; width: 354px; background: var(--navy); }
  .brand-band.green { right: 0; width: 354px; background: var(--green); }
</style>
</head>
<body>
  <main class="letterhead">
    <header class="brand">
      <span class="brand-name">tavi kora</span>
      <span class="brand-dot"></span>
    </header>

    <h1 class="salutation">Dear Mr. Smith,</h1>

    <section class="letter-body">
      <p>Lorem ipsum dolor sit amet, consectetuer adipiscing elit, sed diam nonmmy nibh euismod tincidunt ut laor eet dolore magna aliquam erat volutpat. Ut wisi enim ad minim veniam, quis nostrud exerci tationmcorper suscipit lobortis nisl ut aliquip ex ea commodo consequat. Duis autem vel eum iriure dolor in hendrerit in vulputate velit esse molestie consequat, vel illum dolore eu feugiat</p>
      <p>Rorem ipsum dolor sit amet, consectetuer adipiscing elit, sed diam nonmmy nibh euismod tincidunt ut laor eet dolore magna aliquam erat volutpat. Ut wisi enim ad minim veniam, quis nostrud exerci tationmcorper suscipit lobortis nisl ut aliquip ex ea commodo consequat. Duis autem vel eum iriure dolor in hendrerit in vulputate velit esse molest</p>
      <p>Dorem ipsum dolor sit amet, consectetuer adipiscing elit, sed diam nonmmy nibh euismod tincidunt ut laor eet dolore magna aliquam erat volutpat. Ut wisi enim ad minim veniam, quis nostrud exerci tationmcorper suscipit lobortis nisl ut aliquip ex ea commodo consequat. Duis autem vel eum iriure dolor in hendrerit in suscipit lobortis nisl ut aliquip ex ea commodo consequat. Duis autem vel eum iriure dolor in hendrerit in vulputate velit esse molestie consequat, vel illum</p>
      <p>Sorem ipsum dolor sit amet, consectetuer adipiscing elit, sed diam nonmmy nibh euismod tincidunt ut laor eet dolore magna aliquam erat volutpat. Ut wisi enim ad minim veniam, quis nostrud exerci tationmcorper suscipit lobortis nisl ut aliquip ex ea commodo consequat. Duis autem vel eum iriure dolor in</p>
    </section>

    <p class="closing">Sincerely,</p>
    <div class="signature" role="img" aria-label="Handwritten signature of the sender"></div>

    <div class="footer-rule"></div>
    <ul class="contact-list">
      <li>
        <svg viewBox="0 0 10 10" aria-hidden="true"><path d="M2 1 L4 1 L4.6 3.2 L3.4 4 Q4.3 5.8 6 6.6 L6.8 5.4 L9 6 L9 8 Q9 9 8 9 Q1 8.6 1 2 Q1 1 2 1 Z" fill="var(--green)"/></svg>
        123-456-2100
      </li>
      <li>
        <svg viewBox="0 0 10 10" aria-hidden="true"><rect x="0.5" y="2" width="9" height="6.5" fill="var(--green)"/><path d="M0.5 2 L5 5.6 L9.5 2" stroke="#fff" stroke-width="0.9" fill="none"/></svg>
        info@tavikora.com
      </li>
      <li>
        <svg viewBox="0 0 10 10" aria-hidden="true"><circle cx="5" cy="5" r="4.5" fill="var(--green)"/><path d="M0.5 5 H9.5 M5 0.5 Q2.4 5 5 9.5 M5 0.5 Q7.6 5 5 9.5" stroke="#fff" stroke-width="0.7" fill="none"/></svg>
        www.tavikora.com
      </li>
    </ul>
    <address class="address" style="font-style: normal;">
      Your address<br>city<br>state, ZIP 0000
    </address>

    <div class="brand-band navy"></div>
    <div class="brand-band green"></div>
  </main>
</body>
</html>
```